Australian Trucking Company Requires Professional Looking Stationary

We require a professional looking stationary design that incorporates our newly designed logo.

Our business, called "Brell Haulage Contracting", provides contracting work, transport and logistics to business in Western Australia particularly with links to the mining sector.

We are a small business looking to expand and our new logo and our new stationary will help develop our brand image in our market place.

Target Market(s)

Businesses and Corporation with links to the Mining Sector

Industry/Entity Type

Small Business

Requirements
Must have
• The letterhead must have the following details:
The new logo

Text saying: "Brell Holdings Pty Ltd (ACN 582 316 907) ATF The Brell Discretionary Trust T/AS"
"ABN 71 834 209 553"
Address "P.O Box 817 Wattlegrove WA, 6958"
Phone: 08 9352 7140
Email: brellhaul@mailbox-example.com.au

The text on the letterhead should be editable as the details are likely to change in the near future. Provision should be made for a website address all though one isn't available at the moment.

The styling, layout and font text is entirely up to the designer.

```html
<!DOCTYPE html>
<html lang="en">
<head>
<meta charset="utf-8">
<title>Brell Haulage Contracting – Business Cards</title>
<link rel="stylesheet" href="https://fonts.googleapis.com/css2?family=Source+Sans+3:wght@400;600;700&display=swap">
<style>
  :root {
    --brand-red: #e31b23;
    --brand-red-deep: #c4161d;
    --brand-maroon: #a8181e;
    --ink: #3a3a3a;
    --ink-soft: #6b6b6b;
    --rule-grey: #b5b5b5;
    --paper: #ffffff;
    --backdrop: #eeeeee;
  }
  * { box-sizing: border-box; margin: 0; padding: 0; }
  html, body {
    width: 1200px;
    height: 650px;
    overflow: hidden;
    background: var(--backdrop);
    font-family: "Source Sans 3", "Myriad Pro", Arial, sans-serif;
  }
  .stationery {
    position: relative;
    width: 1200px;
    height: 650px;
  }
  .card {
    position: absolute;
    top: 170px;
    width: 540px;
    height: 310px;
    border-radius: 22px;
    overflow: hidden;
    box-shadow: 0 6px 18px rgba(0,0,0,0.18);
  }

  /* ---------- Front ---------- */
  .card--front {
    left: 45px;
    background: var(--paper);
  }
  .card__wave {
    position: absolute;
    inset: 0;
    width: 100%;
    height: 100%;
  }
  .brand-name {
    position: absolute;
    left: 34px;
    top: 84px;
    color: var(--brand-maroon);
    font-weight: 700;
    font-size: 24px;
    line-height: 1.0;
    text-transform: uppercase;
    letter-spacing: 0.5px;
  }
  .divider {
    position: absolute;
    left: 284px;
    top: 34px;
    width: 2px;
    height: 112px;
    background: linear-gradient(to bottom, var(--rule-grey), rgba(181,181,181,0.15));
  }
  .contact {
    position: absolute;
    left: 296px;
    top: 32px;
    color: var(--ink);
  }
  .contact__name {
    color: var(--brand-red);
    font-weight: 700;
    font-size: 18px;
    line-height: 1.1;
  }
  .contact__title {
    color: var(--ink-soft);
    font-size: 13px;
    margin-bottom: 8px;
  }
  .contact__list { list-style: none; }
  .contact__item {
    display: flex;
    align-items: center;
    gap: 6px;
    font-size: 12px;
    line-height: 1.6;
    white-space: nowrap;
  }
  .contact__icon {
    width: 10px;
    height: 10px;
    flex: none;
    fill: var(--brand-red);
  }
  .front-footer {
    position: absolute;
    left: 30px;
    bottom: 28px;
    color: var(--paper);
    font-size: 13px;
    line-height: 1.9;
  }

  /* ---------- Back ---------- */
  .card--back {
    left: 615px;
    background: linear-gradient(135deg, var(--brand-red-deep), var(--brand-red) 55%, #e8252c);
    color: var(--paper);
  }
  .back-brand {
    position: absolute;
    left: 0;
    right: 0;
    top: 104px;
    text-align: center;
    font-weight: 700;
    font-size: 30px;
    text-transform: uppercase;
    letter-spacing: 0.5px;
  }
  .legal {
    position: absolute;
    left: 0;
    right: 0;
    bottom: 34px;
    text-align: center;
    font-size: 12.5px;
    line-height: 1.75;
  }
</style>
</head>
<body>
<main class="stationery">

  <section class="card card--front" aria-label="Business card front">
    <svg class="card__wave" viewBox="0 0 540 310" preserveAspectRatio="none" aria-hidden="true">
      <defs>
        <linearGradient id="swoosh-grey" x1="0" x2="1" y1="0" y2="0">
          <stop offset="0" stop-color="#4a4a4a"/>
          <stop offset="0.5" stop-color="#bdbdbd"/>
          <stop offset="1" stop-color="#3d3d3d"/>
        </linearGradient>
        <linearGradient id="band-red" x1="0" x2="1" y1="0" y2="1">
          <stop offset="0" stop-color="#c4161d"/>
          <stop offset="0.6" stop-color="#e31b23"/>
          <stop offset="1" stop-color="#d71920"/>
        </linearGradient>
      </defs>
      <path d="M0 198 C100 204 200 214 300 207 S 470 190 540 156 L540 310 L0 310 Z" fill="url(#swoosh-grey)"/>
      <path d="M0 212 C100 218 200 228 300 221 S 470 206 540 172 L540 310 L0 310 Z" fill="url(#band-red)"/>
    </svg>

    <div class="brand-name">Brell<br>Haulage<br>Contracting</div>

    <div class="divider"></div>

    <div class="contact">
      <p class="contact__name">Your Name</p>
      <p class="contact__title">Title</p>
      <ul class="contact__list">
        <li class="contact__item">
          <svg class="contact__icon" viewBox="0 0 24 24" aria-hidden="true"><path d="M6.6 10.8a15.1 15.1 0 0 0 6.6 6.6l2.2-2.2a1 1 0 0 1 1-.25 11.4 11.4 0 0 0 3.6.57 1 1 0 0 1 1 1V20a1 1 0 0 1-1 1A17 17 0 0 1 3 4a1 1 0 0 1 1-1h3.5a1 1 0 0 1 1 1c0 1.250.2 2.450.57 3.57a1 1 0 0 1-.25 1z"/></svg>
          <span>08 9352 7140</span>
        </li>
        <li class="contact__item">
          <svg class="contact__icon" viewBox="0 0 24 24" aria-hidden="true"><path d="M2 5h20v14H2z M2 5l10 8 10-8"/></svg>
          <span>brellhaul@mailbox-example.com.au</span>
        </li>
        <li class="contact__item">
          <svg class="contact__icon" viewBox="0 0 24 24" aria-hidden="true"><path d="M12 2a10 10 0 1 0 0 20 10 10 0 0 0 0-20zm6.9 6h-2.9a15.6 15.6 0 0 0-1.4-3.6A8 8 0 0 1 18.9 8zM12 4c.8 1.2 1.5 2.5 1.9 4h-3.8c.4-1.5 1.1-2.8 1.9-4zM4.3 14a8 8 0 0 1 0-4h3.4a16 16 0 0 0 0 4zm.8 2h2.9c.3 1.3.8 2.5 1.4 3.6A8 8 0 0 1 5.1 16zM8 8H5.1a8 8 0 0 1 4.3-3.6C8.8 5.5 8.3 6.7 8 8zm4 12c-.8-1.2-1.5-2.5-1.9-4h3.8c-.4 1.5-1.1 2.8-1.9 4zm2.3-6H9.7a14.6 14.6 0 0 1 0-4h4.6a14.6 14.6 0 0 1 0 4zm.3 5.6c.6-1.1 1.1-2.3 1.4-3.6h2.9a8 8 0 0 1-4.3 3.6zM16.3 14a16 16 0 0 0 0-4h3.4a8 8 0 0 1 0 4z"/></svg>
          <span>www.brellhaul-example.com.au</span>
        </li>
      </ul>
    </div>

    <div class="front-footer">
      <p>P.O Box 817 Wattlegrove WA, 6958</p>
      <p>ABN 71 834 209 553</p>
    </div>
  </section>

  <section class="card card--back" aria-label="Business card back">
    <p class="back-brand">Brell Haulage Contracting</p>
    <div class="legal">
      <p>Brell Holdings Pty Ltd (ACN 582 316 907) ATF The Brell Discretionary Trust T/AS</p>
      <p>ABN 71 834 209 553</p>
    </div>
  </section>

</main>
</body>
</html>
```